Quiet Braising For The Patient Epicure

Hi, I had a book cover designed on this site, but I want to modify the cover and change the colours. I want to keep the slow cooker and the ingredients on the cover, but I want to simplify it a bit. And, I am open to other ideas. I have attached below a book cover idea I like and I like the colors as well. I want it to be called Quiet Braising, with the language on the right corner: "Curated For Nearly Effortless Meals That Are Greater Than The Sum Of Their Ingredients" I like the circles idea and my name as the author on the curve.

Target Market(s)

Home Cooks

Colors
00AB8E
00BBA5
67D7C9
C6EFE9
E9F9F6
F0912C
F2A743
F7CA91
FBE8D2
FDF5EE
E54698
E96AAD
F1A4CE
F9D9EA
FCEFF6
6B429C
8869AF
B7A5CE
E3DAEB
F3F0F8

Requirements
Must have
• Please use the colors on the Harvest Table Cook Book and I like the design, but I do not want it identical. I like the author name (Marcus T. Hallbright) on the side of the circle on the upper right side of the cover.
Nice to have
• I like the large words "Quiet Braising"

```html
<!DOCTYPE html>
<html lang="en">
<head>
<meta charset="utf-8">
<title>Quiet Braising — Book Cover</title>
<link rel="stylesheet" href="https://fonts.googleapis.com/css2?family=Playfair+Display:wght@400;500&display=swap">
<style>
  :root {
    --stage: #262626;
    --ink: #ffffff;
    --teal: #1d93a6;
    --teal-deep: #0f5e6e;
    --blue: #2a6fbf;
    --amber: #f08a1c;
    --ember: #e8452a;
    --crimson: #e81e3c;
    --magenta: #d92f9c;
    --violet: #6b2a8c;
    --plum: #3a0f3e;
    --umber: #2b1509;
  }
  * { box-sizing: border-box; margin: 0; padding: 0; }
  html, body {
    width: 1200px;
    height: 1200px;
    overflow: hidden;
    background: var(--stage);
  }
  .cover {
    position: absolute;
    left: 213px;
    top: 20px;
    width: 773px;
    height: 1159px;
    overflow: hidden;
    font-family: "Playfair Display", Georgia, serif;
    color: var(--ink);
  }
  .cover-art {
    position: absolute;
    inset: 0;
    background:
      radial-gradient(circle at 28% 14%, var(--teal) 0, transparent 26%),
      radial-gradient(circle at 8% 0%, var(--teal-deep) 0, transparent 30%),
      radial-gradient(circle at 48% 52%, var(--amber) 0, transparent 30%),
      radial-gradient(circle at 70% 48%, var(--ember) 0, transparent 24%),
      radial-gradient(circle at 96% 38%, var(--crimson) 0, transparent 26%),
      radial-gradient(circle at 90% 8%, var(--ember) 0, transparent 16%),
      radial-gradient(circle at 70% 60%, var(--magenta) 0, transparent 26%),
      radial-gradient(circle at 54% 76%, var(--magenta) 0, transparent 24%),
      radial-gradient(circle at 80% 88%, var(--violet) 0, transparent 30%),
      radial-gradient(circle at 8% 70%, var(--blue) 0, transparent 28%),
      radial-gradient(circle at 12% 96%, var(--teal) 0, transparent 26%),
      radial-gradient(circle at 20% 50%, #a06a55 0, transparent 24%),
      linear-gradient(160deg, var(--umber) 0%, var(--plum) 60%, var(--violet) 100%);
  }
  .author {
    position: absolute;
    left: 0;
    top: 0;
    width: 773px;
    height: 500px;
    overflow: visible;
  }
  .author-name {
    font-family: "Playfair Display", Georgia, serif;
    font-size: 34px;
    fill: var(--ink);
    letter-spacing: 1px;
  }
  .title {
    position: absolute;
    left: 0;
    top: 0;
    width: 100%;
    font-weight: 400;
    font-size: 144px;
    letter-spacing: -0.035em;
    line-height: 1;
  }
  .title-line {
    position: absolute;
    white-space: nowrap;
  }
  .title-line--first { left: 138px; top: 254px; }
  .title-line--second { left: 54px; top: 353px; }
  .tagline {
    position: absolute;
    right: 47px;
    bottom: 34px;
    width: 340px;
    text-align: right;
    font-size: 26px;
    line-height: 36.5px;
    font-weight: 400;
  }
</style>
</head>
<body>
  <main class="cover">
    <div class="cover-art" role="img" aria-label="Abstract painting of overlapping translucent circles in teal, orange, red, magenta and violet, with a faint clock face among them"></div>

    <svg class="author" viewBox="0 0 773 500" aria-label="Marcus T. Hallbright">
      <defs>
        <path id="author-arc" d="M 80 307 A 308 308 0 0 1 614 307" fill="none"/>
      </defs>
      <text class="author-name">
        <textPath href="#author-arc" startOffset="113" textLength="300" lengthAdjust="spacing">Marcus T. Hallbright</textPath>
      </text>
    </svg>

    <h1 class="title">
      <span class="title-line title-line--first">Quiet</span>
      <span class="title-line title-line--second">Braising</span>
    </h1>

    <p class="tagline">Curated For Nearly Effortless Meals That Are Greater Than The Sum Of Their Ingredients</p>
  </main>
</body>
</html>
```